4747 5858

Web(re)design of an existing directory search site www.le5858.be (in Dutch www.de4747.be and in English www.3838.be).

This site is a directory site, i.e. a "white pages" site whereby people can search the phone & details of another person based on a combination of name + city (for instance smith in Brussels); one can also search a company also based on a combination of name + city (for instance Vornak in Brussels); last but not least one can also search the name of the subscriber behind a specific telephone number (also called reverse search).

This site is quite outdated and needs a redesign, see instructions.

We need the output in XD format.

```html
<!DOCTYPE html>
<html lang="fr">
<head>
<meta charset="utf-8">
<title>58-58 — Annuaire</title>
<link href="https://fonts.googleapis.com/css2?family=Oswald:wght@500;600&family=Lato:wght@400;700&display=swap" rel="stylesheet">
<style>
:root{
  --red:#c4161c;
  --ink:#1a1a1a;
  --body:#444;
  --muted:#666;
  --light:#f3f3f3;
  --white:#fff;
  --footer:#000;
}
*{box-sizing:border-box;margin:0;padding:0}
html,body{width:1200px;height:2258px;overflow:hidden}
body{font-family:'Lato',sans-serif;color:var(--body);background:var(--white);position:relative}
.head-font{font-family:'Oswald',sans-serif}

.topbar{height:32px;background:var(--red);color:var(--white);font-size:13px;font-weight:700;text-align:center;line-height:32px}

.site-header{height:75px;position:relative;background:var(--white)}
.brand{position:absolute;left:132px;top:16px;display:flex;align-items:center;gap:6px;font-family:'Oswald',sans-serif;font-weight:600;font-size:30px;color:var(--red)}
.brand-dot{width:14px;height:14px;border-radius:50%;background:var(--red)}
.btn{position:absolute;border-radius:20px;font-size:15px;font-weight:700;display:flex;align-items:center;justify-content:center;text-transform:uppercase}
.btn-login{left:641px;top:20px;width:132px;height:36px;background:var(--red);color:var(--white)}
.btn-signup{left:789px;top:20px;width:132px;height:36px;border:2px solid var(--red);color:var(--red)}
.lang{position:absolute;left:944px;top:26px;display:flex;align-items:center;gap:8px;font-size:13px;font-weight:700;color:#333}
.flag{width:24px;height:24px;border-radius:50%;background:linear-gradient(90deg,#1f3f9a 0 33%,#fff 33% 66%,#d82b2b 66%)}
.menu{position:absolute;left:1049px;top:29px}

.hero{height:480px;position:relative;background:linear-gradient(100deg,#5d6f85 0%,#8b8178 40%,#a9a29a 70%,#7d7770 100%);color:var(--white);text-align:center}
.hero-shade{position:absolute;inset:0;background:rgba(20,25,35,.35)}
.hero h1{position:absolute;top:222px;left:0;right:0;font-family:'Oswald',sans-serif;font-weight:600;font-size:43px;line-height:50px}
.hero p{position:absolute;top:285px;left:158px;width:884px;font-size:13.5px;line-height:24px}
.search-panel{position:absolute;left:158px;top:352px;width:880px;height:83px;border-radius:10px;background:rgba(255,255,255,.3)}
.search-bar{position:absolute;left:19px;top:15px;width:842px;height:55px;border-radius:28px;background:var(--white);display:flex;align-items:center;color:var(--muted);font-size:13px;text-align:left}
.search-type{width:162px;height:100%;background:#f0f0f0;border-radius:28px 0 0 28px;display:flex;align-items:center;padding-left:35px;gap:18px;color:#222;font-weight:700;font-size:14px;text-transform:uppercase}
.field{height:100%;display:flex;align-items:center;padding-left:15px;border-right:1px solid #d5d5d5}
.f1{width:185px}.f2{width:200px;padding-left:30px}.f3{flex:1;border:none;padding-left:38px}
.search-go{width:40px;height:40px;border-radius:50%;background:var(--red);margin-right:8px;display:flex;align-items:center;justify-content:center}

.section-title{text-align:center;font-family:'Oswald',sans-serif;font-weight:600;font-size:31px;color:var(--ink);text-transform:uppercase}
.title-rule{width:36px;height:4px;background:var(--red);margin:12px auto 0}

.pro{height:659px;position:relative}
.pro .section-title{position:absolute;top:47px;left:0;right:0}
.pro .title-rule{position:absolute;top:99px;left:582px;margin:0}
.pro-photo{position:absolute;left:110px;top:135px;width:476px;height:403px;border-radius:10px;background:linear-gradient(120deg,#ece8e2 0%,#e2d7c6 45%,#d9b24a 70%,#c9c3bb 100%)}
.pro-copy{position:absolute;left:624px;top:165px;width:467px}
.pro-copy h2{font-family:'Oswald',sans-serif;font-weight:500;font-size:21px;color:var(--ink);margin-bottom:14px}
.pro-copy p{font-size:13.5px;line-height:24px;text-align:justify;color:var(--body)}
.btn-more{position:static;display:inline-flex;margin-top:24px;width:222px;height:36px;border:2px solid var(--red);color:var(--red)}

.usage{height:637px;background:var(--light);position:relative}
.usage .section-title{position:absolute;top:72px;left:0;right:0}
.usage .title-rule{position:absolute;top:122px;left:582px;margin:0}
.cards{position:absolute;left:133px;top:153px;width:934px;display:grid;grid-template-columns:460px 460px;column-gap:14px;row-gap:13px}
.card{height:123px;background:var(--white);border-radius:4px;position:relative}
.card svg{position:absolute;left:10px;top:18px}
.card h3{position:absolute;left:102px;top:12px;font-family:'Oswald',sans-serif;font-weight:500;font-size:17px;color:var(--ink);text-transform:uppercase}
.card p{position:absolute;left:102px;top:40px;width:345px;font-size:13.5px;line-height:24px;color:#333}

.site-footer{height:375px;background:var(--footer);color:var(--white);position:relative}
.foot-brand{position:absolute;left:180px;top:100px;display:flex;align-items:center;gap:8px;font-family:'Oswald',sans-serif;font-weight:600;font-size:38px;color:var(--red)}
.foot-brand .brand-dot{width:16px;height:16px}
.socials{position:absolute;left:155px;top:196px;display:flex;gap:14px}
.socials span{width:30px;height:30px;border-radius:50%;background:var(--red)}
.foot-col{position:absolute;top:56px}
.foot-col h4{font-family:'Oswald',sans-serif;font-weight:500;font-size:17px;text-transform:uppercase;margin-bottom:12px}
.foot-col li{list-style:none;font-size:14px;line-height:28px;display:flex;gap:10px}
.foot-col li::before{content:"»";color:var(--red)}
.c1{left:377px}.c2{left:610px}.c3{left:839px;width:220px}
.contact li::before{content:none}
.contact li{align-items:flex-start}
.contact svg{flex:none;margin-top:7px}
.foot-rule{position:absolute;left:126px;top:298px;width:982px;height:1px;background:#777}
.copyright{position:absolute;top:318px;left:0;right:0;text-align:center;font-size:13px}
</style>
</head>
<body>
<div class="topbar">Les renseignements CINQUANTE-HUIT utiles</div>

<header class="site-header">
  <div class="brand"><span class="brand-dot"></span>58-58</div>
  <a class="btn btn-login">Connexion</a>
  <a class="btn btn-signup">S'inscrire</a>
  <div class="lang">Français <span class="flag"></span></div>
  <svg class="menu" width="18" height="16" viewBox="0 0 18 16"><rect y="0" width="18" height="3" fill="#333"/><rect y="6.5" width="18" height="3" fill="#333"/><rect y="13" width="18" height="3" fill="#333"/></svg>
</header>

<section class="hero">
  <div class="hero-shade" role="img" aria-label="Photo d'une femme à lunettes travaillant sur un ordinateur portable"></div>
  <h1>WELCOME TO 58-58</h1>
  <p>La douleur elle-même est l'amour de la douleur, les principaux problèmes écologiques, mais je donne ce genre de temps pour tomber, de sorte que de grandes douleurs et douleurs. Qui suspend l'enfant vengeur. Rire s'il vous plaît tirez maecen couche ou lac facile.</p>
  <div class="search-panel">
    <div class="search-bar">
      <div class="search-type">Particuliers <svg width="9" height="5" viewBox="0 0 9 5"><path d="M0 0h9L4.5 5z" fill="#222"/></svg></div>
      <div class="field f1">Nom de famille:</div>
      <div class="field f2">Prénom:</div>
      <div class="field f3">Localité:</div>
      <div class="search-go"><svg width="16" height="16" viewBox="0 0 16 16"><circle cx="6.5" cy="6.5" r="4.5" fill="none" stroke="#fff" stroke-width="2.2"/><path d="M10 10l4 4" stroke="#fff" stroke-width="2.5" stroke-linecap="round"/></svg></div>
    </div>
  </div>
</section>

<section class="pro">
  <h2 class="section-title">Êtes-vous un professionnel?</h2>
  <div class="title-rule"></div>
  <div class="pro-photo" role="img" aria-label="Photo d'une jeune femme en pull jaune travaillant à son bureau"></div>
  <div class="pro-copy">
    <h2>La douleur elle-même est l'amour de la douleur</h2>
    <p>La douleur elle-même est l'amour de la douleur, les principaux problèmes écologiques, mais je donne ce genre de temps pour tomber, de sorte que de grandes douleurs et douleurs. Qui suspend l'enfant vengeur. Risus commodité dessin animé maecenas accumsan lacus vel facilisis Car personne ne rejette, ou ne hait, ou ne fuit le plaisir, parce que c'est le plaisir lui-même, mais parce que de grandes douleurs résultent de ceux qui ne savent pas suivre le plaisir par la raison. De plus, il n'y a personne qui désire obtenir la douleur, parce que la douleur elle-même est amour, augmentée, et désire l'acquérir, mais parce que des moments d'une telle nature ne se produisent pas, de sorte que par le travail et la douleur, il peut rechercher un grand plaisir.</p>
    <a class="btn btn-more">Apprendre encore plus</a>
  </div>
</section>

<section class="usage">
  <h2 class="section-title">Comment puis-je utiliser 58-58 ?</h2>
  <div class="title-rule"></div>
  <div class="cards">
    <div class="card">
      <svg width="80" height="86" viewBox="0 0 80 86" fill="none" stroke="#c4161c" stroke-width="4"><circle cx="40" cy="24" r="18"/><path d="M8 80v-14a14 14 0 0 1 14-14h36a14 14 0 0 1 14 14v14z"/></svg>
      <h3>Trouver une personne</h3>
      <p>La douleur elle-même est l'amour de la douleur, les princi-paux problèmes écologiques, mais je donne ce genre de temps pour tomber.</p>
    </div>
    <div class="card">
      <svg width="80" height="86" viewBox="0 0 80 86" fill="none" stroke="#c4161c" stroke-width="4" stroke-linejoin="round"><path d="M14 22l10-6 10 16-7 6c4 9 10 15 19 20l6-7 16 10-6 10c-26 2-52-24-48-49z"/><path d="M44 12a22 22 0 0 1 22 22M46 22a12 12 0 0 1 10 10"/></svg>
      <h3>Rechercher un numéro de téléphone</h3>
      <p>La douleur elle-même est l'amour de la douleur, les princi-paux problèmes écologiques, mais je donne ce genre de temps pour tomber.</p>
    </div>
    <div class="card">
      <svg width="80" height="86" viewBox="0 0 80 86" fill="none" stroke="#c4161c" stroke-width="3"><path d="M40 62C30 48 26 42 26 32a14 14 0 0 1 28 0c0 10-4 16-14 30z"/><circle cx="40" cy="31" r="6"/><path d="M28 56H20l-8 14h56l-8-14h-8M22 70l14-10M58 70L44 60"/></svg>
      <h3>Rechercher une adresse</h3>
      <p>La douleur elle-même est l'amour de la douleur, les princi-paux problèmes écologiques, mais je donne ce genre de temps pour tomber.</p>
    </div>
    <div class="card">
      <svg width="80" height="86" viewBox="0 0 80 86" fill="none" stroke="#c4161c" stroke-width="3"><path d="M48 40V14H10v58h28"/><path d="M16 22h14M16 30h20M16 48h12M16 56h14M16 64h12"/><circle cx="54" cy="56" r="14"/><path d="M64 66l10 10"/><path d="M50 52a4 4 0 1 1 5 4v4M55 63v1"/></svg>
      <h3>Obtenez une vérification des antécédents</h3>
      <p>La douleur elle-même est l'amour de la douleur, les princi-paux problèmes écologiques, mais je donne ce genre de temps pour tomber.</p>
    </div>
    <div class="card">
      <svg width="80" height="86" viewBox="0 0 80 86" fill="none" stroke="#c4161c" stroke-width="3.5" stroke-linejoin="round"><path d="M6 44L40 12l34 32"/><path d="M14 38v38h52V38"/><path d="M58 22V12h8v18"/><circle cx="40" cy="56" r="13"/><circle cx="40" cy="52" r="4"/><path d="M32 65c2-6 14-6 16 0"/></svg>
      <h3>Filtrer un locataire</h3>
      <p>La douleur elle-même est l'amour de la douleur, les princi-paux problèmes écologiques, mais je donne ce genre de temps pour tomber.</p>
    </div>
    <div class="card">
      <svg width="80" height="86" viewBox="0 0 80 86" fill="none" stroke="#c4161c" stroke-width="3.5" stroke-linejoin="round"><rect x="4" y="24" width="72" height="50" rx="4"/><path d="M28 24V14h24v10M4 40l30 10h12l30-10"/><rect x="34" y="44" width="12" height="8"/></svg>
      <h3>Trouver une entreprise</h3>
      <p>La douleur elle-même est l'amour de la douleur, les princi-paux problèmes écologiques, mais je donne ce genre de temps pour tomber.</p>
    </div>
  </div>
</section>

<footer class="site-footer">
  <div class="foot-brand"><span class="brand-dot"></span>58-58</div>
  <div class="socials"><span></span><span></span><span></span><span></span></div>
  <div class="foot-col c1">
    <h4>Solutions numériques</h4>
    <ul><li>La douleur elle-même</li><li>Est l'amour de la douleur</li><li>Les principaux problèmes</li><li>Ecologiques, mais je donne</li><li>Genre de temps pour tomber,</li><li>Desorte que de</li></ul>
  </div>
  <div class="foot-col c2">
    <h4>Légale</h4>
    <ul><li>À propos de nous</li><li>Termes et conditions</li><li>Politique de confidentialité</li><li>Politique relative aux cookies</li><li>Conditions d'utilisation</li><li>Politique de révision</li></ul>
  </div>
  <div class="foot-col c3 contact">
    <h4>Nous contacter</h4>
    <ul>
      <li><svg width="10" height="14" viewBox="0 0 10 14"><path d="M5 14C1 9 0 7 0 5a5 5 0 0 1 10 0c0 2-1 4-5 9z" fill="#c4161c"/><circle cx="5" cy="5" r="2" fill="#000"/></svg>123 La douleur elle-même est l'amour de la douleur,</li>
      <li style="margin-top:8px"><svg width="13" height="13" viewBox="0 0 13 13"><path d="M2 0l3 3-1.5 2c1 2 2.5 3.5 4.5 4.5L10 8l3 3-2 2C5 13 0 8 0 2z" fill="#c4161c"/></svg>+1 555 010 5858</li>
      <li style="margin-top:12px"><svg width="14" height="11" viewBox="0 0 14 11"><rect width="14" height="11" rx="1" fill="#c4161c"/><path d="M0 1l7 5 7-5" stroke="#000" stroke-width="1.2" fill="none"/></svg>info5858@annuaire.example</li>
    </ul>
  </div>
  <div class="foot-rule"></div>
  <div class="copyright">© Droits d'auteur 2022 58-58 | Tous les droits sont réservés</div>
</footer>
</body>
</html>
```